Envelope Design - Winner can do follow-up business

- Varnoko.com is a Swiss-based online store selling business shirts and accessories for business men
- Please visit the webpage to make yourself familiar with the company. Although the text is in German, with Plimbo translator you should be able to understand the main content.
- Our clients are mainly business men between 30 and 60 years old. Mostly with a high income working in the service industry (banking, insurance, lawyers, etc.). Sometimes there wives purchase the shirts for them ;-)
- The colors and the logo are given, as they are also used for the print materials (please see files in attachment)
- I am running several businesses and often need a talented web designer --> the winner gets substantial follow-up business
your task:
-for our company we need a new envelope design
-It should be simple and modern
-please use one of the logos in the followings.
-suprise me :)

```html
<!DOCTYPE html>
<html lang="en">
<head>
<meta charset="utf-8">
<title>Varnoko Envelope Set</title>
<link rel="stylesheet" href="https://fonts.googleapis.com/css2?family=Questrial&family=Open+Sans:wght@400&display=swap">
<style>
  :root {
    --backdrop: #e9e6e1;
    --paper: #ffffff;
    --edge: #8a8a8a;
    --brand-red: #ec2c24;
    --brand-gold: #e4d463;
    --ink: #3a3a3a;
  }
  html, body {
    margin: 0;
    padding: 0;
    width: 1200px;
    height: 904px;
    overflow: hidden;
    background: var(--backdrop);
  }
  .stage {
    position: relative;
    width: 1200px;
    height: 904px;
  }
  .envelope {
    position: absolute;
    background: var(--paper);
    box-shadow: 0 0 0 1px rgba(0,0,0,0.18), 2px 3px 8px rgba(0,0,0,0.12);
  }
  .envelope--back   { left: 239px; top: 48px;  width: 922px; height: 434px; }
  .envelope--middle { left: 152px; top: 210px; width: 923px; height: 434px; }
  .envelope--front  { left: 18px;  top: 400px; width: 922px; height: 434px; }
  .flap-line {
    position: absolute;
    left: 0; top: 0;
    width: 100%;
    height: 160px;
  }
  .wordmark {
    position: absolute;
    margin: 0;
    font-family: "Questrial", sans-serif;
    font-weight: 400;
    line-height: 1;
    letter-spacing: 0.04em;
    white-space: nowrap;
  }
  .wordmark--back {
    left: 50%; top: 44px;
    transform: translateX(-50%);
    font-size: 46px;
    color: var(--brand-red);
  }
  .wordmark--middle {
    left: 50%; top: 86px;
    transform: translateX(-50%);
    font-size: 28px;
    color: var(--brand-gold);
  }
  .wordmark--front {
    left: 58px; top: 266px;
    font-size: 48px;
    color: var(--brand-gold);
  }
  .side-bar {
    position: absolute;
    left: 20px; top: 0;
    width: 10px; height: 326px;
    background: var(--brand-gold);
  }
  .side-dashes {
    position: absolute;
    left: 20px; top: 328px;
    width: 10px;
    display: flex;
    flex-direction: column;
    gap: 4px;
  }
  .side-dashes span {
    display: block;
    height: 16px;
    background: var(--brand-red);
  }
  .side-dashes span:last-child { height: 5px; }
  .contact {
    position: absolute;
    left: 60px; top: 343px;
    margin: 0; padding: 0;
    list-style: none;
    font-family: "Open Sans", sans-serif;
    font-size: 19px;
    color: var(--ink);
  }
  .contact li {
    display: flex;
    align-items: center;
    gap: 10px;
    height: 31px;
  }
  .contact svg { width: 22px; height: 22px; flex: none; }
</style>
</head>
<body>
<div class="stage">

  <section class="envelope envelope--back" aria-label="Envelope back, red wordmark">
    <svg class="flap-line" viewBox="0 0 922 160" preserveAspectRatio="none">
      <path d="M0 0 C14 46,16 70,70 82 L440 143 Q461 148 482 143 L852 82 C906 70,908 46,922 0" fill="none" stroke="var(--edge)" stroke-width="1"/>
    </svg>
    <p class="wordmark wordmark--back">VARNOKO</p>
  </section>

  <section class="envelope envelope--middle" aria-label="Envelope back, gold wordmark">
    <svg class="flap-line" viewBox="0 0 923 160" preserveAspectRatio="none">
      <path d="M0 0 C14 46,16 70,70 82 L440 143 Q461 148 482 143 L853 82 C907 70,909 46,923 0" fill="none" stroke="var(--edge)" stroke-width="1"/>
    </svg>
    <p class="wordmark wordmark--middle">VARNOKO</p>
  </section>

  <section class="envelope envelope--front" aria-label="Envelope front">
    <div class="side-bar"></div>
    <div class="side-dashes"><span></span><span></span><span></span><span></span></div>
    <p class="wordmark wordmark--front">VARNOKO</p>
    <ul class="contact">
      <li>
        <svg viewBox="0 0 24 24" aria-hidden="true" fill="none" stroke="var(--ink)" stroke-width="1.4">
          <circle cx="12" cy="12" r="10"/>
          <ellipse cx="12" cy="12" rx="4.5" ry="10"/>
          <line x1="2" y1="12" x2="22" y2="12"/>
          <path d="M4 6.5h16M4 17.5h16"/>
        </svg>
        <span>www.varnoko.com</span>
      </li>
      <li>
        <svg viewBox="0 0 24 24" aria-hidden="true">
          <path d="M12 1.5c-4.4 0-7.5 3.3-7.5 7.4 0 5.3 7.5 13.6 7.5 13.6s7.5-8.3 7.5-13.6c0-4.1-3.1-7.4-7.5-7.4z" fill="var(--ink)"/>
          <circle cx="12" cy="9" r="2.8" fill="var(--paper)"/>
        </svg>
        <span>Street Name, City Name, State Zipcode</span>
      </li>
    </ul>
  </section>

</div>
</body>
</html>
```